Brightwater Care Partners, LLC Business Card update!

would like a classier business card. Our cards currently just have our logo and contact information. Need better use of color and creativity
Logo attached.

Target Market(s)

Potential clients, contacts, existing clients. We are a consulting company

Industry/Entity Type

Business

Contact Information for Business Card

We like our colors but just have a boring card with our logo and a white background. I want something that stands out.

Colors
ec1f27
757575

Requirements
Must have
• Color to stay consistent. Logo provided
Nice to have
• Just better use of color/ design

```html
<!DOCTYPE html>
<html lang="en">
<head>
<meta charset="utf-8">
<title>Brightwater Care Partners – Business Card</title>
<link href="https://fonts.googleapis.com/css2?family=Open+Sans:wght@400;600;700&display=swap" rel="stylesheet">
<style>
  :root {
    --brand-red: #ec1f27;
    --band-red: #c42026;
    --brand-grey: #757575;
    --text-grey: #555555;
    --rule: #8a7b74;
    --card: #ffffff;
    --backdrop: #1c1c1c;
  }
  html, body {
    margin: 0;
    width: 1200px;
    height: 900px;
    overflow: hidden;
    background: var(--backdrop);
    font-family: "Open Sans", Arial, sans-serif;
  }
  .business-card {
    position: absolute;
    left: 150px;
    top: 193px;
    width: 900px;
    height: 514px;
    background: var(--card);
    overflow: hidden;
  }
  .brand {
    position: absolute;
    right: 104px;
    top: 78px;
    display: flex;
    align-items: center;
    gap: 14px;
  }
  .brand-dot {
    width: 38px;
    height: 38px;
    border-radius: 50%;
    background: var(--brand-red);
  }
  .brand-name {
    color: var(--brand-red);
    font-weight: 400;
    font-size: 34px;
    line-height: 1;
    letter-spacing: 0.2px;
  }
  .divider {
    position: absolute;
    left: 330px;
    right: 104px;
    top: 218px;
    height: 1px;
    background: var(--rule);
  }
  .person {
    position: absolute;
    left: 112px;
    top: 222px;
  }
  .person-name {
    color: var(--band-red);
    font-weight: 700;
    font-size: 21px;
    line-height: 1.1;
  }
  .person-role {
    color: var(--text-grey);
    font-size: 17px;
    line-height: 1.3;
  }
  .contacts {
    position: absolute;
    right: 76px;
    top: 238px;
    list-style: none;
    margin: 0;
    padding: 0;
    color: var(--text-grey);
    font-size: 17px;
    line-height: 27px;
    text-align: right;
  }
  .contacts li {
    display: flex;
    justify-content: flex-end;
    align-items: center;
    gap: 12px;
  }
  .contacts svg {
    width: 14px;
    height: 14px;
    fill: var(--brand-red);
    flex: none;
  }
  .address-band {
    position: absolute;
    left: 0;
    right: 0;
    bottom: 0;
    height: 112px;
    background: var(--band-red);
    color: #ffffff;
    font-size: 18px;
    display: flex;
    align-items: center;
    justify-content: center;
  }
</style>
</head>
<body>
  <main class="business-card">
    <div class="brand">
      <span class="brand-dot"></span>
      <span class="brand-name">Brightwater Care Partners</span>
    </div>

    <div class="divider"></div>

    <div class="person">
      <div class="person-name">Owner Name</div>
      <div class="person-role">Managing Director</div>
    </div>

    <ul class="contacts">
      <li>000 123 456 456
        <svg viewBox="0 0 16 16" aria-hidden="true"><path d="M1 6c0-3 3-4 7-4s7 1 7 4l-3 1-1-2H5L4 7zM4 8h8l2 6H2z"/></svg>
      </li>
      <li>info@companyname.com
        <svg viewBox="0 0 16 16" aria-hidden="true"><path d="M1 3h14v10H1zM2 4l6 5 6-5z" fill-rule="evenodd"/></svg>
      </li>
      <li>www.companyname.com
        <svg viewBox="0 0 16 16" aria-hidden="true"><path d="M6 10l4-4M7 4l2-2a3 3 0 0 1 5 5l-2 2M9 12l-2 2a3 3 0 0 1-5-5l2-2" fill="none" stroke="#ec1f27" stroke-width="2" stroke-linecap="round"/></svg>
      </li>
    </ul>

    <footer class="address-band">Address line1, Address Line, Country, 012</footer>
  </main>
</body>
</html>
```